RW Framewell Inc Business cards

We need business cards using our existing logo but slightly modified. Right now the logo says RW Loadbearing Masonry. We want to keep the RW part of the design, but replace the Structural Concrete portion with "FRAMEWELL". Please see the attached file.
Ideally this would be a blank template so we can add Different Names, titles, and phone numbers later.
On the one side we want only the logo and on the other side the detail. I'm attaching an example for you to see.
Please reach out with any other questions. Our address and other details will be given out once we find a design we like.

Target Market(s)

Construction Industry

```html
<!DOCTYPE html>
<html lang="en">
<head>
<meta charset="utf-8">
<title>RW Framewell Inc Business Cards</title>
<link href="https://fonts.googleapis.com/css2?family=Archivo:wght@800&family=Arimo:wght@400&display=swap" rel="stylesheet">
<style>
  :root {
    --backdrop: #161616;
    --card: #262626;
    --edge-blue: #1f78c8;
    --brand-blue: #1b77c5;
    --logo-grey: #6e6e6e;
    --text-grey: #8e8e8e;
    --rule: #444444;
  }
  * { box-sizing: border-box; margin: 0; padding: 0; }
  html, body {
    width: 1200px;
    height: 1015px;
    overflow: hidden;
    background: var(--backdrop);
  }
  .sheet {
    position: relative;
    width: 1200px;
    height: 1015px;
  }
  .card {
    position: absolute;
    left: 230px;
    width: 740px;
    height: 423px;
    background: var(--card);
    border-bottom: 4px solid var(--edge-blue);
    box-shadow: 0 14px 30px rgba(0,0,0,0.55);
  }
  .card--front { top: 60px; }
  .card--back { top: 532px; }

  .wordmark {
    font-family: "Archivo", sans-serif;
    font-weight: 800;
    line-height: 1;
    white-space: nowrap;
  }
  .card--front .wordmark {
    position: absolute;
    left: 0; right: 0;
    top: 170px;
    text-align: center;
    font-size: 62px;
    letter-spacing: 2px;
    color: var(--logo-grey);
  }
  .card--back .wordmark {
    position: absolute;
    left: 36px;
    width: 320px;
    top: 194px;
    text-align: center;
    font-size: 31px;
    letter-spacing: 1px;
    color: var(--brand-blue);
  }

  .divider {
    position: absolute;
    left: 388px;
    top: 110px;
    width: 1px;
    height: 200px;
    background: var(--rule);
  }

  .details {
    position: absolute;
    left: 420px;
    top: 118px;
    font-family: "Arimo", sans-serif;
    color: var(--text-grey);
  }
  .details__name {
    font-family: "Archivo", sans-serif;
    font-weight: 800;
    font-size: 24px;
    color: var(--brand-blue);
    letter-spacing: 0.5px;
  }
  .details__title {
    font-size: 18px;
    margin-top: 4px;
  }
  .details__list {
    list-style: none;
    margin-top: 28px;
  }
  .details__item {
    display: flex;
    align-items: center;
    gap: 10px;
    font-size: 17px;
    line-height: 28px;
  }
  .details__item svg {
    width: 16px;
    height: 16px;
    flex: none;
  }
  .details__accent { color: var(--brand-blue); }
</style>
</head>
<body>
<main class="sheet">
  <section class="card card--front" aria-label="Card front">
    <div class="wordmark">RW FRAMEWELL</div>
  </section>

  <section class="card card--back" aria-label="Card back">
    <div class="wordmark">RW FRAMEWELL</div>
    <div class="divider"></div>
    <div class="details">
      <div class="details__name">DANIEL HARTLEY</div>
      <div class="details__title">Managing Director</div>
      <ul class="details__list">
        <li class="details__item">
          <svg viewBox="0 0 16 16" aria-hidden="true"><path fill="var(--brand-blue)" d="M3.6 1.5l2.3 2.6-1.3 1.6c.9 2 2.5 3.6 4.5 4.6l1.6-1.3 2.7 2.2-1.3 2.5C7.4 13.5 2.4 8.6 2.3 3.3z"/></svg>
          044-987 654 321
        </li>
        <li class="details__item">
          <svg viewBox="0 0 16 16" aria-hidden="true"><rect x="1" y="3" width="14" height="10" fill="var(--brand-blue)"/><path d="M1.5 3.5L8 9l6.5-5.5" stroke="var(--card)" stroke-width="1.4" fill="none"/></svg>
          hello@framewell-mail.com
        </li>
        <li class="details__item">
          <svg viewBox="0 0 16 16" aria-hidden="true"><g fill="none" stroke="var(--brand-blue)" stroke-width="1.4"><circle cx="8" cy="8" r="6.5"/><ellipse cx="8" cy="8" rx="3" ry="6.5"/><path d="M1.5 8h13M2.5 4.8h11M2.5 11.2h11"/></g></svg>
          <span>www.<span class="details__accent">framewellbuild</span>.com</span>
        </li>
      </ul>
    </div>
  </section>
</main>
</body>
</html>
```